Roofing company in Toronto, Canada needs a logo design and business card design

We need a business card and logo created for our company. Our company is "KLV Roofing" which provides roofing services for commercial and residential customers. We serve customers in the Greater Toronto Area (in Canada) thus the name KLV.

We want the logo and business card to be a modern design displaying professionalism and quality in the work. We would prefer rounded corners for the business cards but are open to other ideas. The cards should be pleasant and appealing to customers.

Target Market(s)

Commercial and Residential customers

Industry/Entity Type

Roofing

Contact Information for Business Card

Logo Text

KLV Roofing

Requirements
Nice to have
• Colours that are pleasing to the eye but at the same time should stand out from other business cards. If the design can incorporate the name of KLV Roofing and the actual concept of roofing that would be nice.
Should not have
• Do not want the business cards or logo to be childish looking. Need to look professionally designed.

```html
<!DOCTYPE html>
<html lang="en">
<head>
<meta charset="utf-8">
<title>KLV Roofing – Business Card</title>
<link href="https://fonts.googleapis.com/css2?family=Lato:wght@400;700;900&display=swap" rel="stylesheet">
<style>
  :root {
    --page-bg: #d9dde2;
    --card-bg: #eff0f1;
    --ink: #111111;
    --brand-red: #c8161d;
    --title-red: #b3151b;
    --leaf-red: #c91519;
    --leaf-red-deep: #a5121a;
  }
  html, body {
    margin: 0;
    padding: 0;
    width: 1200px;
    height: 970px;
    overflow: hidden;
    background: var(--page-bg);
    font-family: "Lato", sans-serif;
  }
  .canvas {
    position: relative;
    width: 1200px;
    height: 970px;
  }
  .business-card {
    position: absolute;
    left: 80px;
    top: 190px;
    width: 1040px;
    height: 590px;
    background: var(--card-bg);
    border-radius: 28px;
    box-shadow: 0 6px 24px rgba(0, 0, 0, 0.12);
    overflow: hidden;
  }
  .decor-area {
    position: absolute;
    left: 672px;
    top: 0;
    width: 368px;
    height: 590px;
    background: linear-gradient(160deg, var(--leaf-red) 0%, var(--leaf-red-deep) 100%);
  }
  .brand {
    position: absolute;
    left: 44px;
    top: 108px;
    display: flex;
    align-items: center;
    gap: 18px;
  }
  .brand-mark {
    width: 26px;
    height: 26px;
    background: var(--brand-red);
  }
  .brand-name {
    font-size: 80px;
    font-weight: 900;
    color: var(--ink);
    letter-spacing: 1px;
    line-height: 1;
    white-space: nowrap;
  }
  .person {
    position: absolute;
    left: 44px;
    top: 326px;
  }
  .person-name {
    margin: 0;
    font-size: 38px;
    font-weight: 700;
    color: var(--ink);
    line-height: 1;
    letter-spacing: -0.5px;
  }
  .person-title {
    margin: 2px 0 0;
    font-size: 28px;
    font-weight: 400;
    color: var(--title-red);
    line-height: 1.1;
  }
  .contact-list {
    position: absolute;
    left: 44px;
    top: 420px;
    margin: 0;
    padding: 0;
    list-style: none;
  }
  .contact-item {
    display: flex;
    align-items: center;
    gap: 10px;
    height: 36px;
    font-size: 28px;
    color: var(--ink);
    white-space: nowrap;
  }
  .contact-icon {
    width: 30px;
    height: 30px;
    flex: none;
  }
</style>
</head>
<body>
<div class="canvas">
  <section class="business-card">
    <div class="decor-area" role="img" aria-label="Large red maple leaf decoration"></div>

    <div class="brand">
      <span class="brand-mark"></span>
      <span class="brand-name">KLV Roofing</span>
    </div>

    <div class="person">
      <h1 class="person-name">DANIEL REYES</h1>
      <p class="person-title">Managing Director</p>
    </div>

    <ul class="contact-list">
      <li class="contact-item">
        <svg class="contact-icon" viewBox="0 0 30 30" aria-hidden="true">
          <rect width="30" height="30" fill="var(--brand-red)"/>
          <path d="M6 11 Q15 4 24 11 L22 14 L19 12 L19 10 Q15 8 11 10 L11 12 L8 14 Z" fill="#fff"/>
          <rect x="8" y="15" width="14" height="9" rx="1.5" fill="#fff"/>
        </svg>
        <span>(01) 5550 1847</span>
      </li>
      <li class="contact-item">
        <svg class="contact-icon" viewBox="0 0 30 30" aria-hidden="true">
          <rect width="30" height="30" fill="var(--brand-red)"/>
          <rect x="10" y="5" width="10" height="7" fill="#fff"/>
          <rect x="6" y="12" width="18" height="9" rx="1.5" fill="#fff"/>
          <rect x="10" y="19" width="10" height="6" fill="#fff" stroke="var(--brand-red)" stroke-width="1.2"/>
        </svg>
        <span>(01) 5550 1848</span>
      </li>
      <li class="contact-item">
        <svg class="contact-icon" viewBox="0 0 30 30" aria-hidden="true">
          <rect width="30" height="30" fill="var(--brand-red)"/>
          <rect x="5" y="8" width="20" height="14" fill="#fff"/>
          <path d="M5 8 L15 16 L25 8" fill="none" stroke="var(--brand-red)" stroke-width="1.6"/>
        </svg>
        <span>info@klvroofing.ca</span>
      </li>
      <li class="contact-item">
        <svg class="contact-icon" viewBox="0 0 30 30" aria-hidden="true">
          <rect width="30" height="30" fill="var(--brand-red)"/>
          <circle cx="15" cy="15" r="9" fill="none" stroke="#fff" stroke-width="1.6"/>
          <ellipse cx="15" cy="15" rx="4" ry="9" fill="none" stroke="#fff" stroke-width="1.4"/>
          <line x1="6" y1="15" x2="24" y2="15" stroke="#fff" stroke-width="1.4"/>
        </svg>
        <span>www.klvroofing.ca</span>
      </li>
    </ul>
  </section>
</div>
</body>
</html>
```